Online Greeting Card Marketplace redesign

PennedNotes.com is a two-sided greeting card marketplace. Buyers purchase hand-made cards online, indicating their message. Sellers hand-write the message and mail directly to recipient.

We are getting decent foot traffic but low sales. I'm also not drawing a lot of Card Designers to sell their products. Feedback has been that it's cluttered, boring, and out of date.

I've always enjoyed vibes such as Dana Holloway and Gwen Rutledge. I was going for pale blues and chocolate browns (as can be seen in PennedNotes Chatterly and Flitter pages).

Attached document is my not-so-great attempt to redesign, which is uninviting and unpolished.

Need a new homepage and a second similar page when shopping (click on any category to see what I mean, e.g. Halloween).
Updates

Industry/Entity Type

Shopping

Requirements
Must have
• I think my logo (stick drawing of a man with an envelope) is what is currently driving a lot of traffic and should stay in the design, pending minor tweaks.

I'll need all the details of the final design to give to the programmers (font styles, color numbers, etc).

Nice to have
• I was thinking of a dotted frame to surround each picture? White Pearl luminescent or a metallic? I just don't know if it works.

```html
<!DOCTYPE html>
<html lang="en">
<head>
<meta charset="utf-8">
<title>Cat Silhouette – PennedNotes.com</title>
<link rel="stylesheet" href="https://fonts.googleapis.com/css2?family=Source+Sans+3:wght@300;400;600&display=swap">
<style>
  :root {
    --top-rule: #3f3f3f;
    --link-blue: #2f6db5;
    --heading-blue: #1c6ec2;
    --button-blue: #1a6fc7;
    --body-text: #555555;
    --label-text: #4a4a4a;
    --nav-grey: #8e9a9b;
    --field-border: #c9c9c9;
    --dotted: #bdbdbd;
    --footer-bg: #0c0c0c;
    --white: #ffffff;
    --card-orange: #e98a2c;
    --card-orange-deep: #c9641a;
  }
  html, body {
    margin: 0;
    padding: 0;
    width: 1144px;
    height: 1200px;
    overflow: hidden;
    background: var(--white);
  }
  body {
    font-family: "Source Sans 3", "Myriad Pro", Arial, sans-serif;
    color: var(--body-text);
  }
  .page {
    position: relative;
    width: 1000px;
    height: 1049px;
    transform: scale(1.144);
    transform-origin: 0 0;
  }
  .abs { position: absolute; }

  .top-rule { left: 0; top: 0; width: 1000px; height: 4px; background: var(--top-rule); }

  .utility-nav {
    left: 0; top: 20px; width: 1000px;
    display: flex; justify-content: center;
    font-size: 12.5px; text-transform: uppercase; letter-spacing: 0.1px;
  }
  .utility-nav a {
    color: var(--link-blue); text-decoration: none;
    padding: 0 14px; border-left: 1px dotted var(--dotted); line-height: 16px;
  }
  .utility-nav a:first-child { border-left: none; }

  .brand {
    left: 418px; top: 93px;
    display: flex; align-items: center; gap: 14px;
  }
  .brand-mark { width: 26px; height: 26px; border-radius: 50%; background: var(--heading-blue); flex: none; }
  .brand-name { font-size: 30px; font-weight: 400; color: #2b2b2b; line-height: 1; }

  .cart { left: 820px; top: 110px; display: flex; align-items: center; gap: 6px; font-size: 13px; color: #333; }

  .main-nav {
    left: 72px; top: 180px; width: 856px; height: 45px;
    background: var(--nav-grey);
  }
  .main-nav ul { list-style: none; margin: 0; padding: 0 0 0 18px; display: flex; height: 45px; align-items: center; }
  .main-nav li { color: var(--white); font-size: 15px; text-transform: uppercase; margin-right: 44px; letter-spacing: 0.2px; }
  .search {
    position: absolute; left: 658px; top: 8px; width: 188px; height: 28px;
    background: var(--white); border: 1px solid #dcdcdc; border-radius: 4px; box-sizing: border-box;
    display: flex; align-items: center; justify-content: space-between; padding: 0 10px;
    font-size: 11px; font-style: italic; color: #9a9a9a;
  }

  .breadcrumb { left: 71px; top: 247px; font-size: 15px; color: var(--link-blue); text-transform: uppercase; }
  .breadcrumb .sep { margin: 0 8px; }

  .product-frame {
    left: 71px; top: 290px; width: 268px; height: 203px;
    border: 1px dotted var(--dotted); box-sizing: border-box; padding: 2px 4px 3px 4px;
  }
  .product-art {
    position: relative; width: 100%; height: 100%;
    background: linear-gradient(160deg, var(--card-orange) 0%, var(--card-orange-deep) 100%);
  }
  .zoom { position: absolute; left: 103px; top: 80px; }

  .product-info { left: 363px; top: 288px; width: 567px; }
  .product-title { margin: 0 0 9px; font-size: 18.5px; font-weight: 400; color: var(--heading-blue); }
  .product-info p {
    margin: 0 0 7px; font-size: 12.7px; font-weight: 300; line-height: 20px;
    color: var(--body-text); word-break: break-all;
  }

  .section-title {
    left: 363px; width: 565px; margin: 0; font-size: 18.5px; font-weight: 400;
    color: var(--heading-blue); padding-bottom: 4px; border-bottom: 1px dotted var(--dotted);
  }
  .details-title { top: 515px; }
  .options-title { top: 675px; }

  .detail-list { left: 363px; top: 560px; margin: 0; font-size: 12.5px; }
  .detail-row { display: flex; height: 24px; }
  .detail-row dt { width: 108px; font-weight: 300; color: var(--label-text); }
  .detail-row dd { margin: 0; font-weight: 300; color: var(--label-text); }
  .detail-row.strong dt, .detail-row.strong dd { font-weight: 400; color: #333; }
  .detail-row.strong dd.price { color: var(--heading-blue); font-weight: 400; }

  .option-label { left: 363px; font-size: 12.5px; font-weight: 300; color: var(--label-text); }
  .qty-input {
    left: 555px; top: 720px; width: 99px; height: 29px; box-sizing: border-box;
    border: 1px solid var(--field-border); border-radius: 3px; padding: 6px 9px; font-size: 13px; color: #333;
  }
  .checkbox {
    left: 556px; top: 766px; width: 9px; height: 9px; box-sizing: border-box;
    border: 1px solid #999; background: var(--white); padding: 2px;
  }
  .checkbox span { display: block; width: 3px; height: 3px; background: #555; }
  .message-box {
    left: 555px; top: 799px; width: 159px; height: 84px; box-sizing: border-box;
    border: 1px solid var(--field-border); border-radius: 3px; padding: 5px 8px; font-size: 12.5px; color: #555;
  }
  .add-to-cart {
    left: 363px; top: 899px; width: 102px; height: 30px;
    background: var(--button-blue); color: var(--white); font-size: 14px;
    display: flex; align-items: center; justify-content: center;
  }

  .site-footer { left: 0; top: 962px; width: 1000px; height: 87px; background: var(--footer-bg); }
  .footer-links { position: absolute; left: 72px; top: 22px; font-size: 12px; color: var(--white); }
  .copyright { position: absolute; left: 72px; top: 50px; font-size: 11.5px; color: var(--white); }
  .social { position: absolute; right: 72px; top: 36px; display: flex; gap: 14px; font-size: 11.5px; color: var(--white); }
  .social span { display: flex; align-items: center; gap: 5px; }
  .social i { width: 8px; height: 8px; background: #8e9a9b; display: inline-block; }
</style>
</head>
<body>
<div class="page">
  <div class="abs top-rule"></div>

  <nav class="abs utility-nav">
    <a href="#">Home</a><a href="#">How it works</a><a href="#">Sell</a><a href="#">Create an account</a><a href="#">Check out</a><a href="#">Login</a>
  </nav>

  <div class="abs brand">
    <span class="brand-mark"></span>
    <span class="brand-name">PennedNotes.com</span>
  </div>

  <div class="abs cart">
    <svg width="17" height="15" viewBox="0 0 17 15" aria-hidden="true">
      <path d="M1 1.5h3l2 8h8l2-6H5" fill="none" stroke="#c0392b" stroke-width="1.4"/>
      <circle cx="7" cy="12.5" r="1.3" fill="#555"/><circle cx="13" cy="12.5" r="1.3" fill="#555"/>
    </svg>
    <span>Cart (0) items</span>
  </div>

  <nav class="abs main-nav">
    <ul>
      <li>Upcoming Holidays</li><li>Everyday Cards</li><li>Birthdays</li><li>All Categories</li>
    </ul>
    <div class="search">
      <span>Search..</span>
      <svg width="12" height="12" viewBox="0 0 12 12" aria-hidden="true">
        <circle cx="5" cy="5" r="3.8" fill="none" stroke="#999" stroke-width="1.6"/>
        <path d="M8 8l3 3" stroke="#999" stroke-width="1.8"/>
      </svg>
    </div>
  </nav>

  <div class="abs breadcrumb">Home<span class="sep">::</span>Halloween<span class="sep">::</span>Cat Silhouette</div>

  <div class="abs product-frame">
    <div class="product-art" role="img" aria-label="Card photo: black cut-paper cat with arched back under an orange moon">
      <svg class="zoom" width="40" height="40" viewBox="0 0 40 40" aria-hidden="true">
        <circle cx="16" cy="16" r="13" fill="none" stroke="#f2f2f2" stroke-width="3"/>
        <path d="M16 9v14M9 16h14" stroke="#f2f2f2" stroke-width="3"/>
        <path d="M25.5 25.5l11 11" stroke="#f2f2f2" stroke-width="4.5" stroke-linecap="round"/>
      </svg>
    </div>
  </div>

  <section class="abs product-info">
    <h1 class="product-title">Cat Silhouette by Penned Notes</h1>
    <p>This is a cut paper greeting card, with a silhouette of a cat with arched back under an orange moon. Great gothic gift for Halloween or any special dark occasion! Each card is one of my original designs, cut into acid free card stock, with a layer of paper inside. This black card features a layer of patterned orange yellow paper inside. The inside of the patterned paper is white. This is patterned scrapbook paper, and each one will be slightly different as it is cut from different sections of the pattern.</p>
    <p>This card is signed by the artist on the back. Perfect for any occasion, it is blank inside. It measures 5 ½″ x 4 ¼″, and come with an envelope.</p>
    <p>Please e-mail me with any questions, and take a look at my other items for sale.</p>
  </section>

  <h2 class="abs section-title details-title">Details</h2>
  <dl class="abs detail-list">
    <div class="detail-row"><dt>Card Number :</dt><dd>SKU17739</dd></div>
    <div class="detail-row"><dt>Weight :</dt><dd>1.50 lbs</dd></div>
    <div class="detail-row strong"><dt>Card Designer :</dt><dd>By PennedNotes</dd></div>
    <div class="detail-row strong"><dt>Our price :</dt><dd class="price">$6.75</dd></div>
  </dl>

  <h2 class="abs section-title options-title">Options</h2>
  <div class="abs option-label" style="top:725px">Quantity :</div>
  <div class="abs qty-input">1</div>
  <div class="abs option-label" style="top:761px">Send blank card unsealed :</div>
  <div class="abs checkbox"><span></span></div>
  <div class="abs option-label" style="top:796px">Message to Recipient :</div>
  <div class="abs message-box">Enter your message here</div>
  <div class="abs add-to-cart">Add to Cart</div>

  <footer class="abs site-footer">
    <div class="footer-links">About us | FAQ | Contact us</div>
    <div class="copyright">Copyrights 2013. All Rights Reserved.</div>
    <div class="social">
      <span><i></i>Chatterly</span><span><i></i>Flitter</span><span><i></i>Feed</span><span><i></i>ClipStream</span>
    </div>
  </footer>
</div>
</body>
</html>
```